RW Framewell Inc Business cards

We need business cards using our existing logo but slightly modified. Right now the logo says RW Loadbearing Masonry. We want to keep the RW part of the design, but replace the Structural Concrete portion with "FRAMEWELL". Please see the attached file.
Ideally this would be a blank template so we can add Different Names, titles, and phone numbers later.
On the one side we want only the logo and on the other side the detail. I'm attaching an example for you to see.
Please reach out with any other questions. Our address and other details will be given out once we find a design we like.

Target Market(s)

Construction Industry

```html
<!DOCTYPE html>
<html lang="en">
<head>
<meta charset="utf-8">
<title>RW Framewell Inc — Business Cards</title>
<link rel="stylesheet" href="https://fonts.googleapis.com/css2?family=Arimo:wght@400;700&display=swap">
<style>
  :root {
    --backdrop: #2a2d33;
    --brand-blue: #1077c1;
    --card-white: #ffffff;
    --ink: #2b2b2b;
    --rule-grey: #8a8a8a;
  }
  * { box-sizing: border-box; margin: 0; padding: 0; }
  html, body {
    width: 1200px; height: 1000px; overflow: hidden;
    background: var(--backdrop);
    font-family: "Arimo", Arial, sans-serif;
  }
  .canvas {
    position: relative; width: 1200px; height: 1000px;
  }
  .card {
    position: absolute; left: 250px; width: 700px; height: 400px;
    border-radius: 22px; overflow: hidden;
    box-shadow: 0 14px 30px rgba(0,0,0,.45);
  }
  .card--front { top: 60px; background: var(--brand-blue); }
  .card--back { top: 540px; background: var(--card-white); }

  .wordmark {
    display: flex; align-items: center; gap: 14px;
    font-weight: 700; letter-spacing: .12em; white-space: nowrap;
  }
  .wordmark__square { display: block; }
  .card--front .wordmark {
    position: absolute; left: 50%; top: 50%;
    transform: translate(-50%, -50%);
    color: var(--card-white); font-size: 46px;
  }
  .card--front .wordmark__square { width: 30px; height: 30px; background: var(--card-white); }

  .card--back .wordmark {
    position: absolute; left: 44px; top: 52px;
    color: var(--brand-blue); font-size: 30px;
  }
  .card--back .wordmark__square { width: 20px; height: 20px; background: var(--brand-blue); }

  .divider {
    position: absolute; left: 30px; top: 232px;
    width: 440px; height: 2px; background: var(--rule-grey);
  }
  .contact {
    position: absolute; left: 44px; top: 180px;
    list-style: none; color: var(--ink); font-size: 17px; line-height: 1.3;
  }
  .contact__address { margin-bottom: 6px; }
  .contact__item { display: flex; align-items: center; gap: 8px; }
  .contact__item svg { width: 14px; height: 14px; flex: none; }

  .contact { top: 256px; }

  .person {
    position: absolute; right: 44px; top: 196px; text-align: right;
  }
  .person__name {
    color: var(--brand-blue); font-weight: 700; font-size: 28px; letter-spacing: .02em;
  }
  .person__title {
    color: var(--ink); font-size: 18px; margin-top: 4px;
  }
  .edge-tab {
    position: absolute; right: 0; top: 214px; width: 12px; height: 50px;
    background: var(--brand-blue);
  }
</style>
</head>
<body>
<main class="canvas">
  <section class="card card--front" aria-label="Card front">
    <div class="wordmark"><span class="wordmark__square"></span>RW FRAMEWELL</div>
  </section>

  <section class="card card--back" aria-label="Card back">
    <div class="wordmark"><span class="wordmark__square"></span>RW FRAMEWELL</div>
    <div class="divider"></div>

    <ul class="contact">
      <li class="contact__address">418 Keystone Avenue<br>Harlow County 6184</li>
      <li class="contact__item">
        <svg viewBox="0 0 16 16" aria-hidden="true"><path fill="#1077c1" d="M3.5 1.5l2.5 3-1.5 1.5c.8 1.9 2.6 3.7 4.5 4.5l1.5-1.5 3 2.5-1.5 2.5C7 13.5 2.5 9 1 3z"/></svg>
        555-018-2046
      </li>
      <li class="contact__item">
        <svg viewBox="0 0 16 16" aria-hidden="true"><rect x="1" y="3" width="14" height="10" fill="#1077c1"/><path d="M1 3l7 6 7-6" fill="none" stroke="#fff" stroke-width="1.3"/></svg>
        info@rwframewell.com
      </li>
      <li class="contact__item">
        <svg viewBox="0 0 16 16" aria-hidden="true"><circle cx="8" cy="8" r="7" fill="#1077c1"/><path d="M1 8h14M8 1c-3 3.5-3 10.5 0 14M8 1c3 3.5 3 10.5 0 14" fill="none" stroke="#fff" stroke-width="1"/></svg>
        www.rwframewell.com
      </li>
    </ul>

    <div class="person">
      <p class="person__name">DANA MERCER</p>
      <p class="person__title">Owner/CEO</p>
    </div>
    <div class="edge-tab"></div>
  </section>
</main>
</body>
</html>
```